Interior designer needs a power point template design

I need a template PowerPoint design for my client presentations. The presentations I prepare for my clients usually include the furniture project, the detail of the selected furniture, and the costs. There are a lot of images I insert. What I need is to have a template that I can use for all my presentations, where from time to time I will insert the specific images and descriptions I want to insert. What will always be the same will be the cover, the colors, the font, and the design of the internal sections.
I already have my logo that I would like to insert on each page of the presentation (in small size).
In summary, I need:
- basic template design
- cover with an image chosen by Pictavale photo
- design an internal section/chapter
- internal page design.

I like the clolors of pink and brown <8please see image attached)
Images (will come from Pictavale photo)
● entrance/hall
● living room
● dining room
● Bathroom
● Closet
● Kids room
● Master bedroom
● Master bathroom
● Kitchen
● Office
● Laundry
● Balcony or Terrace

Target Market(s)

Customers (both residential and commercial projects)

Industry/Entity Type

interior design

Font styles to use
Other font styles liked:
• I like courier new

Requirements
Must have
• beautiful design
Should not have
• animations

```html
<!DOCTYPE html>
<html lang="it">
<head>
<meta charset="utf-8">
<title>Casa Quieta – Camera Padronale</title>
<link href="https://fonts.googleapis.com/css2?family=Oswald:wght@300&family=Mulish:wght@400&display=swap" rel="stylesheet">
<style>
  :root {
    --backdrop: #9e5f43;
    --cream: #f9e6c8;
    --ink: #2e2622;
    --line: #c9a58c;
    --accent: #a9614a;
    --blush: #e8dcdc;
  }
  * { box-sizing: border-box; margin: 0; padding: 0; }
  html, body { width: 1200px; height: 3924px; overflow: hidden; }
  body { background: var(--backdrop); font-family: "Mulish", sans-serif; color: var(--ink); position: relative; }

  .slide { position: absolute; left: 107px; width: 986px; height: 555px; background: var(--cream); overflow: hidden; box-shadow: 0 2px 6px rgba(0,0,0,.18); }

  .brand { position: absolute; left: 22px; top: 20px; width: 90px; text-align: center; font-family: "Oswald", sans-serif; font-weight: 300; color: var(--ink); font-size: 19px; line-height: 1.05; letter-spacing: 1px; }
  .brand-dot { width: 52px; height: 52px; border: 1px solid var(--ink); border-radius: 50%; margin: 0 auto 10px; }
  .brand-box { background: #fff; padding: 10px 4px; }

  .title { position: absolute; font-family: "Oswald", sans-serif; font-weight: 300; font-size: 42px; line-height: 1; letter-spacing: .5px; text-transform: uppercase; white-space: nowrap; }
  .subtitle { position: absolute; font-family: "Oswald", sans-serif; font-weight: 300; font-size: 19px; text-transform: uppercase; white-space: nowrap; }
  .right { text-align: right; }

  .copy { position: absolute; font-size: 9px; line-height: 15.5px; }
  .copy p + p { margin-top: 14px; }
  .copy.justify p { text-align: justify; text-align-last: right; }
  .copy.left p { text-align: justify; text-align-last: left; }

  .rule-h { position: absolute; height: 1px; background: var(--line); }
  .rule-v { position: absolute; width: 1px; background: var(--line); }

  .art { position: absolute; }
  .lamp { position: absolute; background: linear-gradient(#f1dcc0, #e9d2b4); border-radius: 4px; opacity: .8; }

  .page-no { position: absolute; left: 948px; top: 517px; width: 28px; height: 28px; border-radius: 50%; background: var(--accent); color: var(--cream); font-size: 8px; display: flex; align-items: center; justify-content: center; }
</style>
</head>
<body>

<!-- Slide 1: cover -->
<section class="slide" style="top:81px">
  <div class="brand"><div class="brand-dot"></div>CASA<br>QUIETA</div>
  <h1 class="title" style="left:27px;top:228px">Camera Padronale</h1>
  <div class="copy left" style="left:27px;top:282px;width:350px">
    <p>A calm, layered palette sets the tone for the room, pairing warm oak, soft linen and brushed brass. Each piece is chosen for comfort and scale, leaving clear paths around the bed and generous light from the window.</p>
    <p>Storage is built into the walls to keep surfaces quiet. Lighting is set in three layers, with a ceiling pendant, bedside lamps and a low glow that makes evenings feel slower and more restful.</p>
  </div>
  <div class="lamp" style="left:740px;top:0;width:180px;height:150px" role="img" aria-label="Line drawing of two pendant lamps"></div>
  <div class="art" style="left:405px;top:165px;width:560px;height:350px;border-radius:40px 120px 20px 20px;background:linear-gradient(135deg,#f3d6b4,#e7b98e 55%,#5c8fc8)" role="img" aria-label="Illustration of a bedroom with a bed, plants, window and nightstand"></div>
  <div class="page-no">01</div>
</section>

<!-- Slide 2 -->
<section class="slide" style="top:713px">
  <div class="brand"><div class="brand-dot"></div>CASA<br>QUIETA</div>
  <h2 class="title right" style="right:122px;top:32px">Camera Padronale</h2>
  <p class="subtitle right" style="right:122px;top:82px">L’arredamento della camera padronale</p>
  <div class="lamp" style="left:905px;top:0;width:70px;height:115px" role="img" aria-label="Line drawing of a pendant lamp"></div>
  <div class="rule-h" style="left:490px;top:175px;width:496px"></div>
  <div class="rule-v" style="left:893px;top:95px;height:460px"></div>
  <div class="art" style="left:35px;top:204px;width:440px;height:295px;background:linear-gradient(160deg,#5a5753,#8a6d58 55%,#b39577)" role="img" aria-label="Rendering of a master bedroom with a wooden bed and dark wall"></div>
  <div class="copy justify" style="left:521px;top:208px;width:348px">
    <p>A calm, layered palette sets the tone for the room, pairing warm oak, soft linen and brushed brass. Each piece is chosen for comfort and scale, leaving clear paths around the bed and generous light from the window.</p>
    <p>Storage is built into the walls to keep surfaces quiet. Lighting is set in three layers, with a ceiling pendant, bedside lamps and a low glow that makes evenings feel slower and more restful.</p>
    <p>Finishes, samples and costs for every item are listed on the following pages for your review.</p>
  </div>
  <div class="page-no">02</div>
</section>

<!-- Slide 3 -->
<section class="slide" style="top:1345px">
  <div class="brand"><div class="brand-dot"></div>CASA<br>QUIETA</div>
  <h2 class="title right" style="right:122px;top:32px">Camera Padronale</h2>
  <p class="subtitle right" style="right:122px;top:82px">L’arredamento della camera padronale</p>
  <div class="lamp" style="left:905px;top:0;width:70px;height:115px" role="img" aria-label="Line drawing of a pendant lamp"></div>
  <div class="rule-h" style="left:30px;top:193px;width:510px"></div>
  <div class="rule-v" style="left:128px;top:150px;height:405px"></div>
  <div class="copy justify" style="left:160px;top:224px;width:350px">
    <p>A calm, layered palette sets the tone for the room, pairing warm oak, soft linen and brushed brass. Each piece is chosen for comfort and scale, leaving clear paths around the bed and generous light from the window.</p>
    <p>Storage is built into the walls to keep surfaces quiet. Lighting is set in three layers, with a ceiling pendant, bedside lamps and a low glow that makes evenings feel slower and more restful.</p>
    <p>Finishes, samples and costs for every item are listed on the following pages for your review.</p>
  </div>
  <div class="art" style="left:568px;top:136px;width:321px;height:381px;background:linear-gradient(180deg,#cfd2d8,#9fa3aa 45%,#3d4248 70%,#9a6a44)" role="img" aria-label="Rendering of a bedroom with chandelier, dark bed and open wardrobe"></div>
  <div class="page-no">03</div>
</section>

<!-- Slide 4: section divider -->
<section class="slide" style="top:1977px;background:var(--blush)">
  <div class="art" style="left:0;top:0;width:986px;height:555px;background:linear-gradient(180deg,#e8dcdc 0%,#e8dcdc 78%,#ecc9b4 78%,#e6bda6 100%)" role="img" aria-label="Illustration of a bedroom corner with sun mirror, plant and clothes rack"></div>
  <div class="brand brand-box" style="left:41px;top:3px;width:107px"><div class="brand-dot"></div>CASA<br>QUIETA</div>
  <h2 class="title right" style="right:122px;top:32px">Camera Padronale</h2>
  <div class="lamp" style="left:905px;top:0;width:70px;height:115px;background:#ddcfcf" role="img" aria-label="Line drawing of a pendant lamp"></div>
  <div class="page-no">04</div>
</section>

<!-- Slide 5 -->
<section class="slide" style="top:2607px">
  <div class="brand" style="left:52px"><div class="brand-dot"></div>CASA<br>QUIETA</div>
  <h2 class="title right" style="right:159px;top:32px">Cabina Armadio</h2>
  <p class="subtitle right" style="right:159px;top:82px">L’arredamento della camera padronale</p>
  <div class="lamp" style="left:905px;top:0;width:70px;height:115px" role="img" aria-label="Line drawing of a pendant lamp"></div>
  <div class="rule-h" style="left:411px;top:146px;width:533px"></div>
  <div class="rule-v" style="left:828px;top:80px;height:475px"></div>
  <div class="copy justify" style="left:59px;top:192px;width:347px">
    <p>A calm, layered palette sets the tone for the room, pairing warm oak, soft linen and brushed brass. Each piece is chosen for comfort and scale, leaving clear paths around the bed and generous light from the window.</p>
    <p>Storage is built into the walls to keep surfaces quiet. Lighting is set in three layers, with a ceiling pendant, bedside lamps and a low glow that makes evenings feel slower and more restful.</p>
    <p>Finishes, samples and costs for every item are listed on the following pages for your review.</p>
  </div>
  <div class="art" style="left:506px;top:156px;width:344px;height:344px;border-radius:50%;background:#2a2a2c"></div>
  <div class="art" style="left:503px;top:150px;width:344px;height:344px;border-radius:50%;background:linear-gradient(180deg,#e9ebee,#4a4c52 40%,#d9dbe0 60%,#3a3b40)" role="img" aria-label="Rendering of a walk-in closet with hanging clothes"></div>
  <div class="lamp" style="left:850px;top:405px;width:125px;height:140px" role="img" aria-label="Line drawing of an egg chair"></div>
  <div class="page-no">05</div>
</section>

<!-- Slide 6 -->
<section class="slide" style="top:3254px">
  <div class="brand" style="left:52px"><div class="brand-dot"></div>CASA<br>QUIETA</div>
  <h2 class="title right" style="right:159px;top:32px">Cabina Armadio</h2>
  <p class="subtitle right" style="right:159px;top:82px">L’arredamento della camera padronale</p>
  <div class="lamp" style="left:905px;top:0;width:70px;height:115px" role="img" aria-label="Line drawing of a pendant lamp"></div>
  <div class="rule-h" style="left:0;top:175px;width:470px"></div>
  <div class="rule-v" style="left:52px;top:110px;height:445px"></div>
  <div class="art" style="left:50px;top:187px;width:348px;height:348px;border-radius:50%;background:#b7776a"></div>
  <div class="art" style="left:56px;top:180px;width:344px;height:344px;border-radius:50%;background:linear-gradient(120deg,#2f2d2c,#7a5b3c 45%,#e6e4e2 70%,#4a4b55)" role="img" aria-label="Rendering of a walk-in closet with coats, shoes and shelving"></div>
  <div class="copy justify" style="left:488px;top:203px;width:348px">
    <p>A calm, layered palette sets the tone for the room, pairing warm oak, soft linen and brushed brass. Each piece is chosen for comfort and scale, leaving clear paths around the bed and generous light from the window.</p>
    <p>Storage is built into the walls to keep surfaces quiet. Lighting is set in three layers, with a ceiling pendant, bedside lamps and a low glow that makes evenings feel slower and more restful.</p>
    <p>Finishes, samples and costs for every item are listed on the following pages for your review.</p>
  </div>
  <div class="lamp" style="left:865px;top:400px;width:110px;height:140px" role="img" aria-label="Line drawing of an egg chair"></div>
  <div class="page-no">06</div>
</section>

</body>
</html>
```